Seeking funky, innovative business cards

I am looking to refresh our current business cards to something more engaging, visual and impactful. We are a management consultancy firm, see website (www.larkstone-partners.com.au). I've included our colour scheme, sample of the slides we use and our old business cards. We would like our cards to have icons. The card should display:- Name- Title- Mobile number- Address- Email address- Website - Company logo- Our purpose statement "we build workplaces where people love to be"

Contact Information for Business Card

Brennan Ulfsson
Consultant
0468 927 341
Level 3, 218 Wexley Street, Melbourne 3000
brennan@larkstone-partners.com.au
www.larkstone-partners.com.au

Purpose statement "we build workplaces where people love to be"
LOGO available in google images

Font styles to use
Other font styles liked:
• Open Sans Light, Bebas Neue (open to other cool foints)

Colors
ffc214
5c5c5c
f5f5f5
fefefe

Requirements
Must have
• - Name
• - Title
• - Mobile number
• - Address
• - Email address
• - Website
• - Company logo
• - Our purpose statement "we build workplaces where people love to be"
Nice to have
• - Icons
• - Colour (see our colour scheme"

```html
<!DOCTYPE html>
<html lang="en">
<head>
<meta charset="UTF-8">
<title>Larkstone Partners — Business Card</title>
<link href="https://fonts.googleapis.com/css2?family=Open+Sans:wght@300;400;600&display=swap" rel="stylesheet">
<style>
  :root {
    --stage: #2a2b2e;
    --card: #1f2123;
    --card-edge: #2c2e31;
    --gloss: #0d0e0f;
    --yellow: #ffc214;
    --gold-line: #b8912a;
    --light: #f5f5f5;
    --white: #fefefe;
    --muted: #d8d8d8;
  }
  * { box-sizing: border-box; margin: 0; padding: 0; }
  html, body {
    width: 1200px; height: 800px; overflow: hidden;
    background: var(--stage);
    font-family: "Open Sans", Arial, sans-serif;
  }
  .stage {
    width: 1200px; height: 800px;
    display: flex; align-items: center; justify-content: center; gap: 30px;
  }
  .card {
    position: relative;
    width: 560px; height: 320px;
    background: var(--card);
    border: 1px solid var(--card-edge);
    border-radius: 14px;
    box-shadow: 0 18px 40px rgba(0,0,0,.45);
    white-space: nowrap;
  }

  /* Front */
  .card-front {
    display: flex; flex-direction: column; align-items: center; justify-content: center; gap: 22px;
  }
  .brand-front {
    display: flex; align-items: center; gap: 12px;
    font-weight: 300; font-size: 44px; letter-spacing: .5px;
    color: var(--gloss);
  }
  .brand-front .brand-dot {
    width: 14px; height: 14px; border-radius: 50%; background: var(--gloss);
  }
  .purpose {
    font-weight: 600; font-size: 15px; color: var(--white); letter-spacing: .3px;
  }

  /* Back */
  .card-back {
    display: flex; align-items: center; padding: 0 30px;
  }
  .brand-back {
    display: flex; align-items: center; gap: 9px;
    font-weight: 300; font-size: 24px; color: var(--white);
    margin-top: 80px; flex: none;
  }
  .brand-back .brand-dot {
    width: 11px; height: 11px; border-radius: 50%; background: var(--yellow); flex: none;
  }
  .divider {
    width: 1px; height: 150px; background: var(--gold-line);
    margin: 0 18px 0 16px; flex: none;
  }
  .contact { color: var(--muted); font-size: 12px; line-height: 1.6; }
  .contact .name { font-size: 19px; font-weight: 600; color: var(--white); line-height: 1.2; }
  .contact .title { font-size: 14px; color: var(--yellow); margin-bottom: 8px; }
  .contact .address { margin-bottom: 4px; }
  .contact-row { display: flex; align-items: center; gap: 7px; }
  .icon {
    width: 15px; height: 15px; border-radius: 50%; background: var(--yellow);
    display: flex; align-items: center; justify-content: center; flex: none;
  }
  .icon svg { width: 9px; height: 9px; }
</style>
</head>
<body>
<main class="stage">
  <section class="card card-front">
    <div class="brand-front"><span class="brand-dot"></span>Larkstone Partners</div>
    <p class="purpose">we build workplaces where people love to be</p>
  </section>

  <section class="card card-back">
    <div class="brand-back"><span class="brand-dot"></span>Larkstone Partners</div>
    <div class="divider"></div>
    <div class="contact">
      <p class="name">Brennan Ulfsson</p>
      <p class="title">Consultant</p>
      <p class="address">Level 3, 218 Wexley Street<br>Melbourne 3000</p>
      <p class="contact-row">
        <span class="icon"><svg viewBox="0 0 10 10"><path d="M2 1l2 2-1 1.2c.6 1.2 1.6 2.2 2.8 2.8L7 6l2 2-1.2 1.3C4.5 9 1 5.5.7 2.2z" fill="#1f2123"/></svg></span>
        0468 927 341
      </p>
      <p class="contact-row">
        <span class="icon"><svg viewBox="0 0 10 10"><rect x="1" y="2.5" width="8" height="5" fill="none" stroke="#1f2123" stroke-width="1"/><path d="M1 2.5l4 3 4-3" fill="none" stroke="#1f2123" stroke-width="1"/></svg></span>
        brennan@larkstone-partners.com.au
      </p>
      <p class="contact-row">
        <span class="icon"><svg viewBox="0 0 10 10"><circle cx="5" cy="5" r="3.8" fill="none" stroke="#1f2123" stroke-width="1"/><ellipse cx="5" cy="5" rx="1.6" ry="3.8" fill="none" stroke="#1f2123" stroke-width=".8"/><path d="M1.2 5h7.6" stroke="#1f2123" stroke-width=".8"/></svg></span>
        www.larkstone-partners.com.au
      </p>
    </div>
  </section>
</main>
</body>
</html>
```